Creative Brief
Buisness Card Harbor Crest Homes
Card for Harbor Crest
Professional
Lem Porter
Constrution Supervisor
Harbor Crest Homes
PO Box 564302
Houston, Texas 77341
lporter@harborcrest-homes.example
www.harborcrest-homes.example

```html
<!DOCTYPE html>
<html lang="en">
<head>
<meta charset="utf-8">
<title>Harbor Crest Homes Stationery</title>
<link href="https://fonts.googleapis.com/css2?family=Open+Sans:wght@400;600;700&display=swap" rel="stylesheet">
<style>
  :root{
    --stage:#3b3a39;
    --paper:#ffffff;
    --ink:#1a1a1a;
    --band-dark:#111111;
    --band-mid:#262626;
    --gold:#e0a526;
    --gold-deep:#b87a12;
    --grey:#9a9a9a;
    --rule:#c9c9c9;
  }
  *{box-sizing:border-box;margin:0;padding:0}
  html,body{width:1200px;height:871px;overflow:hidden}
  body{background:var(--stage);font-family:"Open Sans",Arial,sans-serif;position:relative;color:var(--ink)}
  .sheet{position:absolute;background:var(--paper);box-shadow:0 4px 14px rgba(0,0,0,.45)}
  .band{position:absolute;left:0;right:0;background:linear-gradient(180deg,var(--band-mid),var(--band-dark))}
  .brand{display:flex;align-items:center;gap:6px;color:var(--gold);font-weight:700;text-transform:uppercase;letter-spacing:.5px;white-space:nowrap}
  .brand-mark{background:var(--gold);display:inline-block}
  .brand-box{position:absolute;background:#000;border:1px solid var(--gold-deep);display:flex;align-items:center;justify-content:center}

  /* letterhead */
  .letterhead{left:24px;top:41px;width:533px;height:739px}
  .letterhead .band{top:30px;height:84px}
  .letterhead .brand-box{left:26px;top:-8px;width:110px;height:100px}
  .letterhead .brand{font-size:11px}
  .letterhead .brand-mark{width:9px;height:9px}
  .lh-contact{position:absolute;right:30px;top:10px;color:#ddd;font-size:7px;line-height:11px;text-align:right}
  .lh-contact .row{display:flex;justify-content:flex-end;align-items:center;gap:5px}
  .lh-contact svg{width:7px;height:7px;fill:var(--paper)}
  .lh-foot{position:absolute;left:0;right:0;bottom:22px;height:30px}
  .lh-foot .site{position:absolute;left:0;right:0;bottom:-14px;text-align:center;color:var(--gold-deep);font-size:7px}

  /* cards */
  .card{position:absolute;width:206px;height:137px;background:#0b0b0b;overflow:hidden;box-shadow:0 4px 10px rgba(0,0,0,.5)}
  .card .band{top:0;bottom:0}
  .card .brand{font-size:9px}
  .card .brand-mark{width:8px;height:8px}
  .card-a{left:629px;top:103px}
  .card-b{left:857px;top:103px}
  .card-c{left:629px;top:259px}
  .card-d{left:857px;top:259px}
  .card .frame{position:absolute;inset:6px;border:1px solid var(--gold-deep)}
  .card .center-brand{position:absolute;left:0;right:0;top:40px;display:flex;justify-content:center}
  .card .brand-box{width:86px;height:56px}
  .card .site{position:absolute;left:0;right:0;bottom:16px;text-align:center;color:var(--gold);font-size:7px}
  .card .side-brand{left:14px;top:18px}
  .card .person{position:absolute;left:112px;top:16px;color:#eee;font-size:6px;line-height:9px}
  .card .person .name{color:var(--gold);font-size:10px;font-weight:700;line-height:13px}
  .card .person .title{color:var(--grey);margin-bottom:5px}
  .card svg.trim{position:absolute;left:0;bottom:0;width:206px;height:30px}

  /* envelope */
  .envelope{left:403px;top:403px;width:425px;height:221px}
  .flap{position:absolute;left:0;top:0;width:425px;height:70px}
  .envelope .brand-box{left:166px;top:6px;width:92px;height:50px}
  .envelope .brand{font-size:8px}
  .envelope .brand-mark{width:7px;height:7px}

  /* compliment slip */
  .slip{left:614px;top:480px;width:562px;height:288px}
  .slip .band{top:26px;height:56px}
  .slip .brand-box{left:231px;top:-8px;width:100px;height:68px}
  .slip .brand{font-size:10px}
  .slip .brand-mark{width:8px;height:8px}
  .slip .addr{position:absolute;left:0;right:0;top:87px;text-align:center;font-size:6px;color:#555}
  .slip .foot{position:absolute;left:0;right:0;bottom:14px;height:16px}
</style>
</head>
<body>

<section class="sheet letterhead" aria-label="Letterhead">
  <div class="band" role="img" aria-label="Dark patterned header band">
    <div class="brand-box"><span class="brand"><i class="brand-mark"></i>Harbor Crest</span></div>
    <div class="lh-contact">
      <div>Nolan Reyes</div>
      <div>PO Box 564302</div>
      <div>Houston, Texas 77341</div>
      <div class="row">281-555-0142 <svg viewBox="0 0 10 10"><rect width="10" height="10"/></svg></div>
      <div class="row">832-555-0187 <svg viewBox="0 0 10 10"><rect width="10" height="10"/></svg></div>
      <div class="row">lporter@harborcrest-homes.example <svg viewBox="0 0 10 10"><rect width="10" height="10"/></svg></div>
    </div>
  </div>
  <div class="lh-foot">
    <svg width="533" height="30" viewBox="0 0 533 30">
      <polyline points="0,26 266,14 533,26" fill="none" stroke="var(--rule)" stroke-width="2"/>
      <polyline points="266,18 533,28" fill="none" stroke="var(--gold)" stroke-width="3"/>
    </svg>
    <div class="site">www.harborcrest-homes.example</div>
  </div>
</section>

<section class="card card-a" aria-label="Business card front">
  <div class="band" role="img" aria-label="Dark patterned card background"></div>
  <div class="frame"></div>
  <div class="center-brand"><div class="brand-box" style="position:static"><span class="brand"><i class="brand-mark"></i>Harbor Crest</span></div></div>
  <div class="site">www.harborcrest-homes.example</div>
</section>

<section class="card card-b" aria-label="Business card back">
  <div class="band" role="img" aria-label="Dark patterned card background"></div>
  <div class="frame"></div>
  <div class="brand-box side-brand"><span class="brand"><i class="brand-mark"></i>Harbor Crest</span></div>
  <div class="person">
    <div class="name">Lem Porter</div>
    <div class="title">Construction Supervisor</div>
    <div>Harbor Crest Homes</div>
    <div>PO Box 564302</div>
    <div>Houston, Texas 77341</div>
    <div>281-555-0142</div>
    <div>lporter@harborcrest-homes.example</div>
  </div>
</section>

<section class="card card-c" aria-label="Business card front, alternate">
  <div class="band" role="img" aria-label="Dark patterned card background"></div>
  <div class="center-brand" style="top:30px"><div class="brand-box" style="position:static"><span class="brand"><i class="brand-mark"></i>Harbor Crest</span></div></div>
  <svg class="trim" viewBox="0 0 206 30"><path d="M0,22 Q103,4 206,22" fill="none" stroke="var(--gold)" stroke-width="2"/></svg>
  <div class="site" style="bottom:4px">www.harborcrest-homes.example</div>
</section>

<section class="card card-d" aria-label="Business card back, alternate">
  <div class="band" role="img" aria-label="Dark patterned card background"></div>
  <div class="brand-box side-brand"><span class="brand"><i class="brand-mark"></i>Harbor Crest</span></div>
  <div class="person">
    <div class="name">Lem Porter</div>
    <div class="title">Construction Supervisor</div>
    <div>PO Box 564302</div>
    <div>Houston, Texas 77341</div>
    <div>281-555-0142</div>
    <div>lporter@harborcrest-homes.example</div>
  </div>
  <svg class="trim" viewBox="0 0 206 30"><path d="M0,24 Q103,8 206,24 L206,30 L0,30Z" fill="var(--gold)"/></svg>
</section>

<section class="sheet envelope" aria-label="Envelope">
  <svg class="flap" viewBox="0 0 425 70" role="img" aria-label="Dark patterned envelope flap">
    <path d="M0,0 H425 L212,70 Z" fill="var(--band-dark)"/>
  </svg>
  <div class="brand-box"><span class="brand"><i class="brand-mark"></i>Harbor Crest</span></div>
</section>

<section class="sheet slip" aria-label="Compliment slip">
  <div class="band" role="img" aria-label="Dark patterned header band">
    <div class="brand-box"><span class="brand"><i class="brand-mark"></i>Harbor Crest</span></div>
  </div>
  <div class="addr">Harbor Crest Homes &nbsp; PO Box 564302 &nbsp; Houston, Texas 77341</div>
  <svg class="foot" width="562" height="16" viewBox="0 0 562 16">
    <polyline points="0,13 281,4 562,13" fill="none" stroke="var(--rule)" stroke-width="2"/>
    <polyline points="281,7 562,15" fill="none" stroke="var(--gold)" stroke-width="3"/>
  </svg>
</section>

</body>
</html>
```